Simple and Clean business card design

We would like the design to be simple clean and to incorporate our colors.

We are open to your design and talent, we have the dots in our logo as we think of it as data points and we connect data points for people.

We are open to see the great creative and clean design you bring to the table

Contact Information for Business Card

please include: name, position, email, phone and website

Font styles to use
Sans Serif

Requirements
Must have
• my colors incorporated, simplicity
Nice to have
• lots of white space, simplicity
Should not have
• complexicity/ complex art

```html
<!DOCTYPE html>
<html lang="en">
<head>
<meta charset="utf-8">
<title>Tandrowe Business Card</title>
<link href="https://fonts.googleapis.com/css2?family=Montserrat:wght@400;500;700&display=swap" rel="stylesheet">
<style>
  :root {
    --page-bg: #35312e;
    --card-bg: #1d1e20;
    --white: #ffffff;
    --muted: #9a9a9c;
    --green: #34a853;
    --blue: #5a7fc4;
    --rule: #d9d9d9;
  }
  * { box-sizing: border-box; margin: 0; padding: 0; }
  html, body {
    width: 1200px; height: 900px; overflow: hidden;
    background: var(--page-bg);
    font-family: "Montserrat", sans-serif;
  }
  .sheet {
    width: 1200px; height: 900px;
    display: flex; flex-direction: column; align-items: center; justify-content: center;
    gap: 40px;
  }
  .card {
    width: 700px; height: 400px;
    background: var(--card-bg);
    border-radius: 4px;
    box-shadow: 0 10px 30px rgba(0,0,0,.45);
    position: relative;
    overflow: hidden;
  }
  .wordmark {
    display: flex; align-items: center; gap: 12px;
    color: var(--white); font-weight: 700; letter-spacing: 1px;
    white-space: nowrap;
  }
  .wordmark__dot { border-radius: 50%; background: var(--blue); flex: none; }
  .card--front .wordmark {
    position: absolute; left: 50%; top: 160px; transform: translateX(-50%);
    font-size: 68px; line-height: 1;
  }
  .card--front .wordmark__dot { width: 34px; height: 34px; }
  .front__url {
    position: absolute; left: 0; right: 0; top: 290px;
    text-align: center; color: var(--muted);
    font-size: 15px; letter-spacing: 7px; font-weight: 500;
  }
  .card--back .wordmark {
    position: absolute; left: 40px; top: 240px;
    font-size: 50px; line-height: 1;
  }
  .card--back .wordmark__dot { width: 26px; height: 26px; }
  .back__rule {
    position: absolute; left: 392px; top: 70px; width: 2px; height: 260px;
    background: var(--rule);
  }
  .contact {
    position: absolute; left: 420px; top: 74px; color: var(--white);
  }
  .contact__name { font-size: 24px; font-weight: 700; letter-spacing: .5px; }
  .contact__name-first { color: var(--green); }
  .contact__role { font-size: 18px; margin-top: 4px; }
  .contact__address { font-size: 15px; line-height: 1.35; margin-top: 26px; }
  .contact__list { list-style: none; margin-top: 26px; font-size: 15px; }
  .contact__list li { display: flex; align-items: center; gap: 10px; line-height: 1.7; }
  .contact__icon { width: 14px; height: 14px; fill: var(--green); flex: none; }
</style>
</head>
<body>
<main class="sheet">
  <section class="card card--front">
    <div class="wordmark"><span class="wordmark__dot"></span><span>tandrowe</span></div>
    <p class="front__url">www.tandrowe.one</p>
  </section>

  <section class="card card--back">
    <div class="wordmark"><span class="wordmark__dot"></span><span>tandrowe</span></div>
    <div class="back__rule"></div>
    <div class="contact">
      <p class="contact__name"><span class="contact__name-first">MARCUS</span> ELLERY</p>
      <p class="contact__role">Founder/ CEO</p>
      <p class="contact__address">128 Elm Avenue<br>Fairview, OH 44120</p>
      <ul class="contact__list">
        <li>
          <svg class="contact__icon" viewBox="0 0 24 24"><path d="M6.6 10.8a15.1 15.1 0 0 0 6.6 6.6l2.2-2.2a1 1 0 0 1 1-.25 11.4 11.4 0 0 0 3.6.57 1 1 0 0 1 1 1V20a1 1 0 0 1-1 1A17 17 0 0 1 3 4a1 1 0 0 1 1-1h3.5a1 1 0 0 1 1 1c0 1.25.2 2.45.57 3.6a1 1 0 0 1-.25 1z"/></svg>
          555-214-3908
        </li>
        <li>
          <svg class="contact__icon" viewBox="0 0 24 24"><path d="M2 5h20v14H2zM4 7v.4l8 5 8-5V7l-8 5z"/></svg>
          marcus.ellery@tandrowe.one
        </li>
        <li>
          <svg class="contact__icon" viewBox="0 0 24 24"><circle cx="12" cy="12" r="10"/></svg>
          www.tandrowe.one
        </li>
      </ul>
    </div>
  </section>
</main>
</body>
</html>
```